Business Management Fortress

Assist with enhancing a powerpoint slide by providing a few design options for consideration. I have a template but open to any creative ideas.

Internal employees and stakeholders

Business Management, Finance, Accounting

• Maintain a fortress, temple, or pyramid schema
• Scenic Background

```html
<!DOCTYPE html>
<html lang="en">
<head>
<meta charset="utf-8">
<title>Business Management Fortress</title>
<link href="https://fonts.googleapis.com/css2?family=Poppins:wght@500;600&display=swap" rel="stylesheet">
<style>
  :root {
    --fortress-navy: #2f275f;
    --label-orange: #e0561f;
    --sky-top: #eef0f6;
    --sky-mid: #e6e7f0;
    --lake-mist: #d9d8e3;
    --shore-tone: #cfcdd6;
  }
  html, body {
    margin: 0;
    padding: 0;
    width: 1200px;
    height: 675px;
    overflow: hidden;
  }
  .slide {
    position: relative;
    width: 1200px;
    height: 675px;
    overflow: hidden;
    font-family: "Poppins", sans-serif;
  }
  .scenic-backdrop {
    position: absolute;
    inset: 0;
    background:
      radial-gradient(ellipse 60% 40% at 50% 30%, rgba(255,255,255,0.6), rgba(255,255,255,0) 70%),
      linear-gradient(180deg, var(--sky-top) 0%, var(--sky-mid) 50%, var(--shore-tone) 66%, var(--lake-mist) 78%, var(--sky-mid) 100%);
  }
  .fortress {
    position: absolute;
    inset: 0;
    width: 1200px;
    height: 675px;
  }
  .fortress .structure { fill: var(--fortress-navy); }
  .fortress .label {
    fill: var(--label-orange);
    font-family: "Poppins", sans-serif;
    font-weight: 600;
  }
  .fortress .label-tier { font-size: 29px; font-weight: 500; letter-spacing: 0.5px; }
  .fortress .label-pillar { font-size: 25px; }
  .fortress .label-detail { font-size: 20.5px; font-weight: 500; }
</style>
</head>
<body>
<div class="slide">
  <div class="scenic-backdrop" role="img" aria-label="Misty lakeside temple with tiered pagoda roofs under a pale sky"></div>

  <svg class="fortress" viewBox="0 0 1920 1080" xmlns="http://www.w3.org/2000/svg" aria-label="Business management fortress pyramid">
    <g class="structure">
      <!-- legs -->
      <polygon points="785,213 843,213 672,697 615,697"/>
      <polygon points="1015,213 1072,213 1240,697 1183,697"/>
      <!-- roof cap -->
      <rect x="738" y="155" width="404" height="58" rx="29"/>
      <!-- finial dome -->
      <path d="M896,293 L896,275 A30,30 0 0 1 956,275 L956,293 Z"/>
      <!-- tier two band -->
      <path d="M663,390 L685,322 Q694,293 728,293 L1150,293 Q1190,293 1197,325 L1210,390 L1100,390 L1062,350 L795,353 L722,390 Z"/>
      <!-- tier three band -->
      <path d="M553,522 L567,455 Q576,425 612,425 L1295,425 Q1336,425 1346,462 L1366,520 L1180,522 L1110,486 L745,486 L675,522 Z"/>
      <!-- tier four band -->
      <path d="M463,650 L477,592 Q487,553 530,553 L1390,553 Q1431,553 1441,592 L1457,648 L1225,650 L1160,614 L700,614 L630,650 Z"/>
      <!-- pillar divider -->
      <rect x="911" y="610" width="31" height="90"/>
      <!-- base -->
      <path d="M298,903 L315,748 Q320,697 372,697 L1550,697 Q1605,697 1608,752 L1622,903 L1238,903 L1222,800 L1208,757 L650,757 L637,790 L637,903 Z"/>
      <!-- ground bar -->
      <rect x="254" y="903" width="1412" height="57" rx="29"/>
    </g>

    <g class="labels">
      <text class="label label-tier" x="607" y="485">LEADER</text>
      <text class="label label-tier" x="1117" y="485">PROFITABILITY</text>
      <text class="label label-tier" x="928" y="524" text-anchor="middle">PARTNER</text>

      <text class="label label-pillar" x="537" y="610">People</text>
      <text class="label label-pillar" x="1183" y="606">Strategic Alliances</text>
      <text class="label label-pillar" x="762" y="659">Innovation</text>
      <text class="label label-pillar" x="1035" y="644" text-anchor="middle">Business</text>
      <text class="label label-pillar" x="1035" y="676" text-anchor="middle">Intelligence</text>

      <text class="label label-pillar" x="948" y="801" text-anchor="middle">Fiduciary Responsibilities</text>
      <text class="label label-detail" x="935" y="843" text-anchor="middle">Accurate Financials/Internal Controls / Brand</text>
      <text class="label label-detail" x="935" y="879" text-anchor="middle">Protection /Compliance/Ethics / Cost Management</text>
    </g>
  </svg>
</div>
</body>
</html>
```